Printer Cartridges Supplier Namecard

Attached is my company logo and the design of my current namecard. I would like to have a more special look for it. Can have a little cuteness too rather than those normal standard feel. I'm a supplier mainly dealing with original and compatible printer toner cartridges, some other products like paper supplies as well.

Target Market(s)

Companies, businesses, corporates

Industry/Entity Type

It Company

Contact Information for Business Card

Logo, name, contact, address, supplies and maybe a slogan

Colors
85cae6
33a6d7
3176b5
0255a3
0792cd
85abd2

Requirements
Must have
• Logo, name, contact and address basic details.
• Must include some pictures, not just rearrange what I'm currently having.
Nice to have
• Be creative and bold, a diiferent traditional feel.

```html
<!DOCTYPE html>
<html lang="en">
<head>
<meta charset="utf-8">
<title>tonerbay.sg — Namecard</title>
<link rel="stylesheet" href="https://fonts.googleapis.com/css2?family=Lato:wght@400;700&display=swap">
<style>
  :root {
    --stage: #08151d;
    --paper: #ffffff;
    --brand-blue: #29a9e0;
    --accent-blue: #2a9fd8;
    --ink-grey: #58595b;
    --text-grey: #4a4a4a;
    --rule-grey: #b5b5b5;
    --illus-light: #eef3f7;
    --illus-mid: #c9d6e0;
  }
  html, body {
    margin: 0;
    width: 1200px;
    height: 900px;
    overflow: hidden;
    background: var(--stage);
    font-family: "Lato", Arial, sans-serif;
  }
  .stage { position: relative; width: 1200px; height: 900px; }
  .card {
    position: absolute;
    top: 170px;
    width: 347px;
    height: 561px;
    overflow: hidden;
  }
  .card--front { left: 259px; background: var(--paper); }
  .card--back { left: 631px; background: var(--brand-blue); }

  .brand {
    position: absolute;
    display: flex;
    align-items: center;
    gap: 12px;
    white-space: nowrap;
  }
  .brand__mark { width: 62px; height: 62px; border-radius: 8px; flex: none; }
  .brand__text { display: flex; flex-direction: column; line-height: 1; }
  .brand__name { font-size: 36px; font-weight: 400; letter-spacing: 0.5px; }
  .brand__tagline { font-weight: 700; font-size: 8px; margin-top: 5px; }

  .card--front .brand { left: 34px; top: 40px; }
  .card--front .brand__mark { background: var(--brand-blue); }
  .card--front .brand__name,
  .card--front .brand__tagline { color: var(--ink-grey); }

  .card--back .brand { left: 34px; top: 134px; }
  .card--back .brand__mark { background: var(--paper); }
  .card--back .brand__name,
  .card--back .brand__tagline { color: var(--paper); }

  .person { position: absolute; top: 142px; width: 100%; text-align: center; }
  .person__name { margin: 0; font-size: 22px; font-weight: 700; color: var(--accent-blue); }
  .person__role { margin: 0; font-size: 15px; color: var(--text-grey); }

  .rule {
    position: absolute; left: 116px; width: 130px; height: 1px;
    background: var(--rule-grey);
  }
  .rule--top { top: 205px; }
  .rule--bottom { top: 306px; }

  .contact {
    position: absolute; top: 221px; width: 100%;
    margin: 0; padding: 0; list-style: none;
    text-align: center; font-size: 15px; line-height: 20px; color: var(--text-grey);
  }
  .contact__label { color: var(--accent-blue); font-weight: 700; }

  .address {
    position: absolute; top: 323px; width: 100%;
    margin: 0; font-style: normal; text-align: center;
    font-size: 15px; line-height: 20px; color: var(--text-grey);
  }

  .product-illustration {
    position: absolute; left: 10px; top: 410px; width: 330px; height: 132px;
    background: linear-gradient(160deg, var(--illus-light), var(--illus-mid));
    border-radius: 6px;
  }

  .services {
    position: absolute; left: 46px; top: 249px;
    margin: 0; padding: 0; list-style: none;
  }
  .services__item {
    display: flex; align-items: center; gap: 10px;
    height: 50.5px;
    font-size: 18px; font-weight: 700; color: var(--paper);
    white-space: nowrap;
  }
  .services__item::before {
    content: ""; width: 11px; height: 11px; border-radius: 50%;
    background: var(--paper); flex: none;
  }
</style>
</head>
<body>
<main class="stage">
  <section class="card card--front" aria-label="Namecard front">
    <div class="brand">
      <span class="brand__mark"></span>
      <div class="brand__text">
        <span class="brand__name">tonerbay.sg</span>
        <span class="brand__tagline">Compatible printer ink and toner solutions</span>
      </div>
    </div>

    <div class="person">
      <h1 class="person__name">Mira Tan</h1>
      <p class="person__role">Sales Executive</p>
    </div>

    <div class="rule rule--top"></div>
    <ul class="contact">
      <li><span class="contact__label">P</span>: 9000 1234</li>
      <li><span class="contact__label">E</span>: mira@tonerbay.sg</li>
      <li><span class="contact__label">W</span>: www.tonerbay.sg</li>
    </ul>
    <div class="rule rule--bottom"></div>

    <address class="address">
      12A Harbourview Lane<br>
      #05-118<br>
      Singapore 530012
    </address>

    <div class="product-illustration" role="img"
         aria-label="Illustration of an office printer, CMYK ink cartridges and reams of paper"></div>
  </section>

  <section class="card card--back" aria-label="Namecard back">
    <div class="brand">
      <span class="brand__mark"></span>
      <div class="brand__text">
        <span class="brand__name">tonerbay.sg</span>
        <span class="brand__tagline">Compatible printer ink and toner solutions</span>
      </div>
    </div>

    <ul class="services">
      <li class="services__item">Printer Ink &amp; Toner Catridge</li>
      <li class="services__item">Orginal Printer Catridge</li>
      <li class="services__item">Paper Product</li>
      <li class="services__item">Printer Maintance &amp; Repair</li>
    </ul>
  </section>
</main>
</body>
</html>
```